Rooted Deep Within: Reshape Your Company with the 6 Laws of Harvest

I'm looking for a design that is clean, like the book "Quiet Harbor" by Lena Voskuil. The book is about the principles of organic farming so I am looking for a color scheme that fits that image.
https://www.shelfmerchant.example/Quiet-Harbor-Calm-Waters-Long-ebook/dp/Z00K493QRT/ref=sr_1_3?crid=58PLQ20ZX44MV&keywords=lena+voskuil&qid=1500000000&s=books&sprefix=lena+%2Cstripbooks%2C250&sr=1-3

I don't want a dark color scheme. I prefer a white or cream book with a bold font.

This book is a good example of what I am looking for:

https://www.shelfmerchant.example/Lantern-Notes-Quiet-Making-Days/dp/0000000000/ref=rtpb_2/000-0000000-0000000?pd_rd_w=ab1c2&pf_rd_p=00000000-0000-0000-0000-000000000000&pf_rd_r=AAAAAAAAAAAAAAAAAAAA&pd_rd_r=00000000-0000-0000-0000-000000000000&pd_rd_wg=x1y2z&pd_rd_i=0000000000&psc=1

Target Market(s)

CEOs and business owners who want to increase the trust in their brands

Industry/Entity Type

Management and Leadership

Colors
00AB8E
00BBA5
67D7C9
C6EFE9
E9F9F6
59FF00
82FF00
B8FF75
E3FFCB
F4FFEA
FFF300
FFF600
FEFA6F
FFFEC7
FFFEE8
FFC000
F8CF3A
FAE287
FDF2CF
FEFAEE

Requirements
Must have
• Author's name is: Martin Keelback
Nice to have
• I have indicated some books that I like. I would be good to have a simple image such as an apple core or the earth's core or some other image of "core" but not absolutely necessary.
Should not have
• I don't want it to have a dark cover or be too heavy

```html
<!DOCTYPE html>
<html lang="en">
<head>
<meta charset="utf-8">
<title>Rooted Deep Within – Book Cover</title>
<link rel="stylesheet" href="https://fonts.googleapis.com/css2?family=Jost:ital,wght@0,400;0,500;0,700;1,400&family=Allura&display=swap">
<style>
  :root {
    --stage: #ececec;
    --paper: #ffffff;
    --ink: #1a1a1a;
    --leaf-deep: #1fc94a;
    --leaf-bright: #59ff00;
    --apple-skin: #8fc24a;
    --apple-flesh: #eef0c8;
  }
  * { margin: 0; padding: 0; box-sizing: border-box; }
  html, body {
    width: 1200px;
    height: 794px;
    overflow: hidden;
    background: var(--stage);
  }
  .cover {
    position: absolute;
    left: 335px;
    top: 0;
    width: 530px;
    height: 794px;
    background: var(--paper);
    font-family: "Jost", sans-serif;
    color: var(--ink);
  }
  .subtitle {
    position: absolute;
    top: 56px;
    left: 0;
    width: 100%;
    text-align: center;
    font-size: 20px;
    line-height: 25px;
    font-weight: 400;
  }
  .subtitle em { font-style: italic; }
  .title-top {
    position: absolute;
    top: 108px;
    left: 0;
    width: 100%;
    text-align: center;
    font-size: 112px;
    line-height: 1;
    font-weight: 700;
    letter-spacing: -2px;
    background: linear-gradient(90deg, var(--leaf-deep), var(--leaf-bright) 45%, var(--leaf-deep));
    -webkit-background-clip: text;
    background-clip: text;
    color: transparent;
  }
  .title-script {
    position: absolute;
    top: 214px;
    left: 0;
    width: 100%;
    text-align: center;
    font-family: "Allura", cursive;
    font-size: 96px;
    line-height: 1;
    color: var(--ink);
    z-index: 2;
  }
  .title-bottom {
    position: absolute;
    top: 292px;
    left: 0;
    width: 100%;
    text-align: center;
    font-size: 124px;
    line-height: 1;
    font-weight: 500;
    letter-spacing: -3px;
    color: var(--ink);
  }
  .core-image {
    position: absolute;
    left: 191px;
    top: 481px;
    width: 154px;
    height: 184px;
  }
  .author {
    position: absolute;
    top: 700px;
    left: 0;
    width: 100%;
    text-align: center;
    font-size: 40px;
    font-weight: 500;
    letter-spacing: 9px;
    padding-left: 9px;
  }
</style>
</head>
<body>
  <main class="cover">
    <p class="subtitle">Reshape Your Company with the<br><em>6 Laws of Harvest</em></p>
    <h1>
      <span class="title-top">ROOTED</span>
      <span class="title-script">deep</span>
      <span class="title-bottom">WITHIN</span>
    </h1>
    <svg class="core-image" role="img" aria-label="Photograph of a bitten green apple core" viewBox="0 0 154 184">
      <defs>
        <radialGradient id="apple-tone" cx="50%" cy="50%" r="60%">
          <stop offset="0%" stop-color="var(--apple-flesh)"/>
          <stop offset="100%" stop-color="var(--apple-skin)"/>
        </radialGradient>
      </defs>
      <ellipse cx="77" cy="92" rx="75" ry="90" fill="url(#apple-tone)"/>
    </svg>
    <p class="author">AUTHOR NAME</p>
  </main>
</body>
</html>
```